Brightwell Practice Partners, Inc (www.brightwellpracticepartnrs.example) would like to design a website to convey a level of professionalism to healthcare providers that we are the place form them to visit for Contin. Education, Marketing and Management, Joint Venture Partnerships, etc.
We think we would like a WP Site so that we can use the dynamic and static sides of it's capabilities. We also want to have something that acts as a membership side where members can post their Bio and CV's and prospective employers can post help wanted ads.

Target Market(s)

Pediatricians, Pediatric Dentist, Employers seeking these doctors

Industry/Entity Type

Healthcare

Requirements
Must have
• Services:
Resumes/Bio
Help Wanted
Continuing Education Programs
Marketing & Management

```html
<!DOCTYPE html>
<html lang="en">
<head>
<meta charset="utf-8">
<title>Brightwell Practice Partners, Inc</title>
<link rel="stylesheet" href="https://fonts.googleapis.com/css2?family=Roboto+Condensed:wght@400;700&family=Arimo:wght@400&display=swap">
<style>
:root{
  --sky-top:#8cc8ef;
  --sky-mid:#c9e6f8;
  --page:#ffffff;
  --blue:#3aa3dc;
  --blue-dark:#1d85c4;
  --nav-band:#a9d7f4;
  --ink:#222a30;
  --body:#4b4f53;
  --muted:#8c9094;
  --line:#d8dde1;
  --panel-border:#e3e6e8;
  --footer:#9fd2f2;
  --white:#ffffff;
}
*{box-sizing:border-box;margin:0;padding:0}
html,body{width:1200px;height:992px;overflow:hidden}
body{
  position:relative;
  background:linear-gradient(to bottom,var(--sky-top) 0,var(--sky-mid) 170px,var(--page) 300px,var(--page) 100%);
  font-family:"Arimo",Arial,sans-serif;color:var(--body);
}
.abs{position:absolute}
.cond{font-family:"Roboto Condensed","Arial Narrow",sans-serif}

/* top contact */
.top-contact{left:799px;top:12px;display:flex;align-items:center;gap:12px;font-size:14px;color:var(--ink)}
.top-contact .sep{width:1px;height:16px;background:#5c7a8f}
.phone{display:flex;align-items:center;gap:8px}

/* logo */
.logo{left:200px;top:58px;width:224px;height:91px;border-radius:8px;
  background:linear-gradient(#ffffff,#e6e8ea);box-shadow:0 2px 5px rgba(0,0,0,.18);padding:6px}
.logo-inner{width:100%;height:100%;border:1px dashed #b9bfc4;border-radius:5px;
  display:flex;flex-direction:column;align-items:center;justify-content:center;color:var(--blue-dark);font-weight:700}
.logo-name{font-size:31px;line-height:1;letter-spacing:.5px}
.logo-sub{font-size:13px;margin-top:5px;letter-spacing:.3px}

/* nav */
.main-nav{left:424px;top:87px;width:584px;height:40px;background:var(--nav-band);border-radius:0 8px 8px 0;
  display:flex;align-items:center;padding-left:29px;font-size:14.5px;color:var(--ink)}
.main-nav a{color:inherit;text-decoration:none}
.main-nav a.current{color:var(--white)}
.main-nav .bar{margin:0 22px;color:#4d6a80}

/* hero */
.hero{left:193px;top:187px;width:815px;height:331px;background:var(--white);border-radius:8px;
  box-shadow:0 2px 6px rgba(0,0,0,.22);padding:8px 8px 9px 6px}
.hero-photo{width:100%;height:100%;border-radius:4px;
  background:linear-gradient(100deg,#2b3f6a 0,#6c7c96 22%,#dfe6ea 42%,#eceeef 60%,#c9b9ad 78%,#e9e9e6 100%)}

/* welcome */
.welcome-title{left:0;width:1200px;top:538px;text-align:center;font-size:14px;font-weight:700;color:#111;letter-spacing:.3px}
.welcome-title span{color:var(--blue)}
.welcome-text{left:336px;top:571px;width:530px;text-align:center;font-size:10.5px;line-height:15px;color:var(--body)}

.rule{top:657px;height:4px;border-top:1px solid var(--line);border-bottom:1px solid var(--line)}
.upload-btn{left:504px;top:644px;width:194px;height:33px;background:var(--blue);border:2px solid #8fd0f2;
  color:var(--white);font-size:21px;display:flex;align-items:center;justify-content:center;letter-spacing:.8px}

/* panels */
.tab{height:27px;background:var(--blue);color:var(--white);border:2px solid #9dd6f3;border-bottom:0;
  border-radius:6px 6px 0 0;font-size:11.5px;font-weight:700;display:flex;align-items:center;justify-content:center;letter-spacing:.4px}
.panel{top:733px;height:184px;border:1px solid var(--panel-border);border-radius:4px;padding:5px;background:var(--white)}
.panel-inner{width:100%;height:100%;border:2px dashed #eef0f1}
.thumb{top:760px;width:199px;height:71px;background:linear-gradient(100deg,#9aa9b8,#dfe3e7 45%,#7d8ea3)}
.card-text{top:846px;width:190px;font-size:10.5px;line-height:15px;text-align:justify;color:var(--body)}
.news{left:764px;top:754px;width:227px;list-style:none;font-size:10.5px;line-height:15px;text-align:justify}
.news li{position:relative;margin-bottom:5px}
.news li::before{content:"";position:absolute;left:-12px;top:6px;width:4px;height:4px;background:#777}
.news li.dim{color:var(--muted)}

/* footer */
.footer{left:0;top:934px;width:1200px;height:58px;background:linear-gradient(var(--footer),#b9def5)}
.footer-links{left:202px;top:948px;font-size:10.5px;font-weight:700;color:var(--ink)}
.footer-links .bar{margin:0 9px}
.copyright{left:202px;top:965px;font-size:10px;font-weight:700;color:var(--ink)}
.social{top:949px;width:22px;height:22px;background:var(--white);border:1px solid #b7c6d2;border-radius:3px}
</style>
</head>
<body>

<div class="abs top-contact cond">
  <span class="phone">
    <svg width="15" height="12" viewBox="0 0 15 12" aria-hidden="true"><path d="M1 4 Q7.5-1 14 4 L12 6 L10 4.5 L10 3 Q7.5 2 5 3 L5 4.5 L3 6 Z" fill="#222a30"/><rect x="3" y="6" width="9" height="5" rx="1" fill="#222a30"/></svg>
    555 014 2368
  </span>
  <span class="sep"></span>
  <span>CONTACT US</span>
</div>

<div class="abs logo cond">
  <div class="logo-inner">
    <div class="logo-name">BRIGHTWELL</div>
    <div class="logo-sub">PRACTICE PARTNERS, INC</div>
  </div>
</div>

<nav class="abs main-nav cond">
  <a class="current" href="#">HOME</a><span class="bar">|</span>
  <a href="#">ABOUT US</a><span class="bar">|</span>
  <a href="#">SERVICES</a><span class="bar">|</span>
  <a href="#">HELP</a><span class="bar">|</span>
  <a href="#">RESUME/BIO</a><span class="bar">|</span>
  <a href="#">LOCATION</a>
</nav>

<div class="abs hero">
  <div class="hero-photo" role="img" aria-label="Photo of a nurse in scrubs and a doctor examining a baby held by its mother in a bright clinic"></div>
</div>

<h1 class="abs welcome-title cond">WELCOME TO <span>BRIGHTWELL PRACTICE PARTNERS, INC</span></h1>
<p class="abs welcome-text">Lorem ipsum dolor sit amet, consectetur adipiscing elit. Integer diam arcu, imperdiet a consequat at, faucibus et elit. Quisque sit amet est ut tortor suscipit ultrices non nec mi. Donec euismod ipsum ultricies risus adipiscing auctor. Duis eget dui quis enim luctus faucibus id id velit. Pellentesque habitant morbi tristique senectus et netus et malesuada fames ac turpis egestas. Proin gravida dictum est, id suscipit lorem scelerisque sit amet. Duis luct</p>

<div class="abs rule" style="left:200px;width:294px"></div>
<div class="abs rule" style="left:708px;width:292px"></div>
<div class="abs upload-btn cond">UPLOAD RESUME</div>

<div class="abs tab cond" style="left:218px;top:707px;width:164px;height:26px">MARKETING &amp; MANAGEMENT</div>
<div class="abs panel" style="left:193px;width:512px"><div class="panel-inner"></div></div>
<svg class="abs" style="left:205px;top:815px" width="14" height="22" aria-hidden="true"><path d="M13 1 L1 11 L13 21 Z" fill="#d4d8db"/></svg>
<svg class="abs" style="left:682px;top:815px" width="14" height="22" aria-hidden="true"><path d="M1 1 L13 11 L1 21 Z" fill="#d4d8db"/></svg>
<div class="abs thumb" style="left:234px" role="img" aria-label="Photo of hands signing a document"></div>
<div class="abs thumb" style="left:458px" role="img" aria-label="Photo of hands signing a document"></div>
<p class="abs card-text" style="left:241px">Lorem ipsum dolor sit amet, consectetur adipiscing elit. Integer diam arcu, imperdiet a consequat at, faucibus et eli</p>
<p class="abs card-text" style="left:466px">Lorem ipsum dolor sit amet, consectetur adipiscing elit. Integer diam arcu, imperdiet a consequat at, faucibus et eli</p>

<div class="abs tab cond" style="left:801px;top:707px;width:91px;height:28px">LATEST NEWS</div>
<div class="abs panel" style="left:739px;width:269px"><div class="panel-inner"></div></div>
<ul class="abs news">
  <li>Lorem ipsum dolor sit amet, consectetur adipiscing elit. Integer diam arcu, imperdiet a consequat at, faucibus et eli</li>
  <li class="dim">Lorem ipsum dolor sit amet, consectetur adipiscing elit. Integer diam arcu, imperdiet a consequat at, faucibus et eli</li>
  <li class="dim">Lorem ipsum dolor sit amet, consectetur adipiscing elit. Integer diam arcu, imperdiet a consequat at, faucibus et eli</li>
</ul>

<footer class="abs footer"></footer>
<div class="abs footer-links cond">HOME<span class="bar">|</span>SERVICES<span class="bar">|</span>HELP<span class="bar">|</span>LOCATION<span class="bar">|</span>PRIVACY POLICY<span class="bar">|</span>TERMS</div>
<div class="abs copyright cond">All Rights reserved@ Brightwell Practice Partners, Inc</div>
<div class="abs social" style="left:934px"></div>
<div class="abs social" style="left:969px"></div>

</body>
</html>
```